Business card for Luxury Portable Restroom Trailer company

We are a Luxury Portable Restroom Trailer Company Called FALCRIDGE HIRES. Based in Orange County California. We provide portable restroom trailers for events, such as, Weddings, Concerts, Charity events, Sporting events, Tournaments, Corporate events, ect. We rent and Sell the Luxury restrooms. Our colors are white, grey, and Orange. As you will see in the logo we uploaded.
There are 2 people in the company so the names and titles will change for the 3 people but card will remain the same. Here is the information for each Person: Dwight Penner CFO 555 318-0476
next Person: Leon Marchetti VP 555 318-0476
Next Person: Owen Marchetti CEO 555 318-0476
Information to include on the card: Luxury Restroom Trailers Rental and Sales. Weddings, Concerts, Charity, Sporting and Corp. Events.

```html
<!DOCTYPE html>
<html lang="en">
<head>
<meta charset="utf-8">
<title>Falcridge Hires – Business Card</title>
<link href="https://fonts.googleapis.com/css2?family=Montserrat:wght@400;500;700;800&display=swap" rel="stylesheet">
<style>
  :root {
    --backdrop: #c4c4c4;
    --card: #545456;
    --card-deep: #4b4b4d;
    --orange: #f26a21;
    --white: #ffffff;
    --muted: #e6e6e6;
  }
  * { box-sizing: border-box; margin: 0; padding: 0; }
  html, body { width: 1200px; height: 788px; overflow: hidden; }
  body {
    background: var(--backdrop);
    font-family: "Montserrat", Arial, sans-serif;
    display: flex;
    align-items: center;
    justify-content: center;
    gap: 30px;
  }
  .card {
    width: 560px;
    height: 320px;
    background: var(--card);
    position: relative;
    overflow: hidden;
  }
  /* Front */
  .card-front { padding: 34px 38px; display: flex; flex-direction: column; }
  .brand-name {
    color: var(--orange);
    font-weight: 800;
    font-size: 34px;
    letter-spacing: 1px;
    line-height: 1;
  }
  .identity-row {
    display: flex;
    align-items: center;
    margin-top: 34px;
  }
  .person { min-width: 205px; }
  .person-name {
    color: var(--orange);
    font-weight: 700;
    font-size: 22px;
    letter-spacing: 0.5px;
    text-transform: uppercase;
  }
  .person-title {
    color: var(--white);
    font-size: 14px;
    margin-top: 2px;
    text-align: right;
    padding-right: 14px;
  }
  .divider {
    width: 1px;
    height: 70px;
    background: var(--orange);
    margin: 0 18px 0 4px;
  }
  .contacts { list-style: none; }
  .contacts li {
    color: var(--white);
    font-size: 13px;
    display: flex;
    align-items: center;
    gap: 7px;
    line-height: 22px;
  }
  .contacts svg { width: 11px; height: 11px; fill: var(--orange); flex: none; }
  .services { margin-top: auto; }
  .services-tagline {
    color: var(--orange);
    font-size: 14.5px;
    font-weight: 500;
  }
  .services-events {
    color: var(--white);
    font-size: 17px;
    font-weight: 500;
    margin-top: 4px;
    letter-spacing: 0.3px;
  }
  /* Back */
  .card-back { background: var(--card); }
  .back-pattern {
    position: absolute;
    inset: 0;
    background: radial-gradient(circle at 70% 30%, #5c5c5e, var(--card-deep));
  }
  .back-mark {
    position: absolute;
    right: 40px;
    bottom: 40px;
    display: flex;
    align-items: center;
    gap: 10px;
  }
  .back-mark-dot {
    width: 30px; height: 30px;
    border: 3px solid var(--orange);
    border-radius: 50%;
  }
  .back-mark-name {
    color: var(--orange);
    font-weight: 800;
    font-size: 15px;
    letter-spacing: 0.5px;
  }
</style>
</head>
<body>
  <section class="card card-front" aria-label="Business card front">
    <div class="brand-name">FALCRIDGE HIRES</div>

    <div class="identity-row">
      <div class="person">
        <div class="person-name">Owen Marchetti</div>
        <div class="person-title">CEO</div>
      </div>
      <div class="divider"></div>
      <ul class="contacts">
        <li>
          <svg viewBox="0 0 24 24" aria-hidden="true"><path d="M6.6 10.8a15.1 15.1 0 0 0 6.6 6.6l2.2-2.2a1 1 0 0 1 1-.25 11.4 11.4 0 0 0 3.6.57 1 1 0 0 1 1 1V20a1 1 0 0 1-1 1A17 17 0 0 1 3 4a1 1 0 0 1 1-1h3.5a1 1 0 0 1 1 1c0 1.25.2 2.45.57 3.57a1 1 0 0 1-.25 1z"/></svg>
          555 318-0476
        </li>
        <li>
          <svg viewBox="0 0 24 24" aria-hidden="true"><path d="M2 5h20v14H2z M2 5l10 8 10-8" /></svg>
          owen@falcridgehires.com
        </li>
        <li>
          <svg viewBox="0 0 24 24" aria-hidden="true"><circle cx="12" cy="12" r="10"/></svg>
          www.falcridgehires.com
        </li>
      </ul>
    </div>

    <div class="services">
      <div class="services-tagline">Luxury Restroom Trailers Rental and Sales</div>
      <div class="services-events">Weddings | Concerts | Charity | Sporting | Corp</div>
    </div>
  </section>

  <section class="card card-back" aria-label="Business card back">
    <div class="back-pattern" role="img" aria-label="Tone-on-tone embossed pattern of the brand mark in rows of circles"></div>
    <div class="back-mark">
      <span class="back-mark-dot"></span>
      <span class="back-mark-name">FALCRIDGE HIRES</span>
    </div>
  </section>
</body>
</html>
```